BrivoNest Learning App for Children with Dyslexia

Project Description:

We are seeking a talented UI/UX designer to create engaging and intuitive designs for Brivonest, an innovative educational app designed to help children learn letters and words through a multisensory learning approach. The app aims to be particularly helpful for children with dyslexia, providing a supportive and interactive learning environment.

Key App Features & Design Requirements:

Account Creation Screen: Design a welcoming and straightforward sign-up page that allows users to register with their email or continue with Quarnix. The design should be clean, focusing on user-friendliness and accessibility, adhering to our terms of service and privacy policy.

Main Screen Design: The main screen should allocate at least 4/6 of its height to the interactive drawing area. It needs to display word prompts in both correct and scrambled orders and include options to "Show all Words," "Play all words," and a search function. The interface should be vibrant, engaging, and easy to navigate for children.

Profile Section: Create a user-friendly profile page that allows users to edit their profile image, name, username, email, links, and bio. The design should be clean and encourage user engagement.

BrivoTally Page: This section will display the user's learning progress, including rankings, a learning curve, and recently learned words. It should visually represent progress in a motivating and understandable way, suitable for a younger audience.

Visual and Auditory Feedback Implementation: Incorporate elements that support visual and auditory feedback, using dyslexia-friendly formats. This includes choosing appropriate colors, fonts, and auditory cues.

Accessibility and Customization Settings: Designs should include settings for adjusting visual contrast, font size, and the word list to accommodate individual preferences and needs.

Feel free to add more interactions and/or pages.

Design preferences:

Color Scheme: Use a bright, inviting color palette that stimulates learning and engagement without overwhelming the users.
Font Selection: Opt for fonts that are readable and accessible, particularly for users with dyslexia.
Icons and Graphics: Design custom icons and graphics that are cohesive with the app's theme and purpose. Illustrations should be simple, relatable, and supportive of the learning process.

Target Market(s)

Educational

Industry/Entity Type

Educational

Colors
0054AA
0677BA
7BADD7
CADEEF
E8F1F8
0094D4
00A9DD
6FCCEA
C7EBF8
E9F6FB

Requirements
Must have
• Educational app, a writing area, scoring and account management
Nice to have
• Statistics, Ranking Page, Settings and some nice visual features

```html
<!DOCTYPE html>
<html lang="en">
<head>
<meta charset="utf-8">
<title>BrivoNest App Screens</title>
<link rel="stylesheet" href="https://fonts.googleapis.com/css2?family=Rubik:wght@300;400;500;700;800&family=Roboto:wght@400;500;700&display=swap">
<style>
  :root {
    --navy: #0054AA;
    --blue: #0677BA;
    --sky: #00A9DD;
    --sky-mid: #0094D4;
    --sky-soft: #6FCCEA;
    --pale: #E9F6FB;
    --pale-2: #C7EBF8;
    --mist: #CADEEF;
    --grey-line: #C9D3D8;
    --ink: #222;
    --ink-soft: #444;
    --nav-bar: #C8E2EA;
    --stage: #7d7f82;
    --white: #fff;
  }
  * { box-sizing: border-box; margin: 0; padding: 0; }
  html, body { width: 1200px; height: 872px; overflow: hidden; }
  body {
    background: radial-gradient(ellipse at center, #a3a5a7 0%, var(--stage) 100%);
    font-family: "Roboto", Arial, sans-serif;
    color: var(--ink);
    position: relative;
  }
  .screen {
    position: absolute; top: 87px; width: 327px; height: 698px;
    background: var(--pale); overflow: hidden;
    display: flex; flex-direction: column;
  }
  .screen--signup { left: 57px; }
  .screen--main { left: 436px; }
  .screen--profile { left: 815px; }

  .brand { height: 77px; text-align: center; padding-top: 13px; }
  .brand__name { font-family: "Rubik", sans-serif; font-weight: 800; font-size: 29px; letter-spacing: 0.5px; color: #1d1d1d; line-height: 1; }
  .brand__tag { font-family: "Rubik", sans-serif; font-weight: 300; font-size: 15.5px; letter-spacing: 0.8px; color: #1d1d1d; margin-top: 6px; }

  .titlebar {
    height: 72px; background: var(--navy); color: var(--white);
    display: flex; align-items: center; justify-content: center; position: relative;
    font-family: "Rubik", sans-serif; font-weight: 700; font-size: 23px; letter-spacing: 0.2px;
  }
  .titlebar__menu { position: absolute; left: 19px; top: 25px; }
  .titlebar__points { position: absolute; right: 18px; font-family: "Rubik", sans-serif; font-weight: 400; font-size: 13.5px; }
  .titlebar__back { position: absolute; left: 27px; top: 19px; }

  /* Sign-up */
  .signup { padding: 20px 20px 0; text-align: center; }
  .signup__lead { font-size: 16.5px; color: var(--ink-soft); }
  .field {
    margin: 21px 0 0 0; height: 51px; border: 2px solid var(--grey-line); background: var(--white);
    font-size: 14.5px; color: #777; text-align: left; padding: 15px 21px;
  }
  .btn-primary {
    display: block; width: 100%; height: 49px; border-radius: 25px; margin-top: 12px;
    background: linear-gradient(90deg, var(--sky) 0%, var(--navy) 100%);
    color: var(--white); font-weight: 500; font-size: 16.5px; line-height: 49px; text-align: center;
  }
  .signup__or { margin-top: 9px; font-size: 16.5px; color: var(--ink-soft); }
  .btn-provider {
    margin: 4px -2px 0; height: 54px; border-radius: 28px; background: var(--white);
    border: 3px solid #dde2e4; display: flex; align-items: center; justify-content: center; gap: 10px;
    font-family: "Rubik", sans-serif; font-size: 17px; font-weight: 500; letter-spacing: 0.5px; color: #2a2a2a;
  }
  .btn-provider__dot { width: 18px; height: 18px; border-radius: 50%; background: var(--blue); }
  .signup__legal { margin-top: 9px; font-size: 12.5px; color: var(--ink-soft); line-height: 1.3; }
  .signup__legal span { color: #111; }
  .hero {
    position: absolute; left: -10px; right: -10px; bottom: 0; height: 240px;
    border-top: 11px solid var(--sky);
    border-radius: 50% 50% 0 0 / 90px 90px 0 0;
    background: linear-gradient(160deg, #3c3f44 0%, #5a5d61 45%, #2a8fd0 75%, #d9c2a4 100%);
  }

  /* Main */
  .artwork {
    height: 250px; margin: 14px 20px 0;
    border-radius: 50%;
    background: radial-gradient(circle at 55% 45%, #d6d8da 0%, #a9acaf 38%, var(--pale) 68%);
  }
  .toggle {
    margin: 16px 16px 0; height: 57px; border-radius: 29px; border: 3px solid #dfe6ea; background: var(--pale);
    display: flex; align-items: center; padding: 0 4px 0 22px; justify-content: space-between;
    font-weight: 500; font-size: 14px;
  }
  .toggle__off { color: #555; }
  .toggle__on {
    height: 43px; padding: 0 14px; border-radius: 22px; background: var(--sky); color: var(--white);
    line-height: 43px; box-shadow: 0 0 0 4px var(--pale-2);
  }
  .words { margin: 25px 13px 0; display: grid; grid-template-columns: repeat(3, 96px); gap: 7px 7px; }
  .word {
    height: 49px; border: 3px solid var(--mist); background: var(--pale);
    color: var(--navy); font-size: 13.5px; display: flex; align-items: center; justify-content: center;
  }
  .screen--main .btn-primary { width: 286px; margin: 18px auto 0; border-radius: 26px; height: 49px; }

  .sysnav {
    margin-top: auto; height: 29px; background: var(--nav-bar);
    display: flex; justify-content: center; align-items: center; gap: 54px;
  }

  /* Profile */
  .card {
    margin: 21px 11px 0; height: 470px; background: var(--white); border: 1px solid #e0e6ea;
    position: relative;
  }
  .avatar {
    position: absolute; left: 91px; top: 7px; width: 118px; height: 118px; border-radius: 50%;
    background: radial-gradient(circle at 50% 40%, #7a6a5a 0%, #4d5b42 60%, #2f3a2a 100%);
  }
  .avatar__cam {
    position: absolute; left: 85px; top: 90px; width: 34px; height: 34px; border-radius: 50%;
    background: #e3eaee; display: flex; align-items: center; justify-content: center;
  }
  .avatar__edit { position: absolute; top: 135px; width: 100%; text-align: center; font-size: 15px; text-decoration: underline; color: #222; }
  .rows { position: absolute; top: 190px; left: 14px; right: 20px; }
  .row { display: grid; grid-template-columns: 86px 1fr 26px; align-items: center; height: 39px; }
  .row__label { font-weight: 500; font-size: 15px; }
  .row__value { font-size: 13.5px; color: #333; }
  .row--links { align-items: start; height: auto; padding-top: 10px; }
  .row--links .row__value { line-height: 22.5px; }
  .row__add { color: var(--navy); }
  .row--bio { margin-top: 28px; }
</style>
</head>
<body>

<svg width="0" height="0" style="position:absolute">
  <defs>
    <symbol id="chevron-circle" viewBox="0 0 26 26">
      <circle cx="13" cy="13" r="11.5" fill="none" stroke="#0054AA" stroke-width="2"/>
      <path d="M11 8 L16 13 L11 18" fill="none" stroke="#0054AA" stroke-width="2" stroke-linecap="round"/>
    </symbol>
    <symbol id="sysnav-icons" viewBox="0 0 140 12">
      <rect x="0" y="1" width="10" height="10" fill="#6b7478"/>
      <circle cx="70" cy="6" r="5" fill="#6b7478"/>
      <path d="M130 1 L140 6 L130 11 Z" fill="#6b7478"/>
    </symbol>
  </defs>
</svg>

<!-- Sign-up screen -->
<section class="screen screen--signup">
  <header class="brand">
    <div class="brand__name">BRIVONEST</div>
    <div class="brand__tag">Learn letters and words</div>
  </header>
  <div class="titlebar">CREATE AN ACCOUNT</div>
  <div class="signup">
    <p class="signup__lead">Enter your email to sign up for this app</p>
    <div class="field">email@sample.io</div>
    <div class="btn-primary">SIGN UP WITH EMAIL</div>
    <p class="signup__or">or continue with</p>
    <div class="btn-provider"><span class="btn-provider__dot"></span>QUARNIX</div>
    <p class="signup__legal">By clicking continue, you agree to our and<br><span>Terms of Service Privacy Policy</span></p>
  </div>
  <div class="hero" role="img" aria-label="Photo of a girl reading open books in front of a chalkboard with floating letters"></div>
</section>

<!-- Main screen -->
<section class="screen screen--main">
  <header class="brand">
    <div class="brand__name">BRIVONEST</div>
    <div class="brand__tag">Learn letters and words</div>
  </header>
  <div class="titlebar">
    <svg class="titlebar__menu" width="24" height="22" viewBox="0 0 24 22"><path d="M0 2H24M0 11H24M0 20H24" stroke="#fff" stroke-width="2.5"/></svg>
    MAIN SCREEN
    <span class="titlebar__points">16 Points</span>
  </div>
  <div class="artwork" role="img" aria-label="Illustration of a grey sphere made of letters with letters flying off it"></div>
  <div class="toggle">
    <span class="toggle__off">SHOW ALL WORDS</span>
    <span class="toggle__on">PLAY ALL WORDS</span>
  </div>
  <div class="words">
    <div class="word">WORD 1</div>
    <div class="word">WORD 2</div>
    <div class="word">WORD 3</div>
    <div class="word">WORD 4</div>
    <div class="word">WORD 5</div>
  </div>
  <div class="btn-primary">SHOW ME THE RESULTS</div>
  <nav class="sysnav"><svg width="140" height="12"><use href="#sysnav-icons"/></svg></nav>
</section>

<!-- Profile screen -->
<section class="screen screen--profile">
  <header class="brand">
    <div class="brand__name">BRIVONEST</div>
    <div class="brand__tag">Learn letters and words</div>
  </header>
  <div class="titlebar">
    <svg class="titlebar__back" width="34" height="34" viewBox="0 0 34 34"><circle cx="17" cy="17" r="17" fill="#fff"/><path d="M20 9 L12 17 L20 25" fill="none" stroke="#0054AA" stroke-width="2.5" stroke-linecap="round"/></svg>
    PROFILE
  </div>
  <div class="card">
    <div class="avatar" role="img" aria-label="Profile photo of the user among green leaves"></div>
    <div class="avatar__cam" style="left:85px;top:90px">
      <svg width="16" height="13" viewBox="0 0 16 13"><rect x="0.5" y="2.5" width="15" height="10" rx="1.5" fill="#a9b4ba"/><rect x="5" y="0.5" width="6" height="3" fill="#a9b4ba"/><circle cx="8" cy="7.5" r="3" fill="#e3eaee"/></svg>
    </div>
    <div class="avatar__edit">Edit profile image</div>
    <div class="rows">
      <div class="row"><span class="row__label">Name</span><span class="row__value">Mara Vennick</span><svg width="26" height="26"><use href="#chevron-circle"/></svg></div>
      <div class="row"><span class="row__label">Username</span><span class="row__value">@username</span><svg width="26" height="26"><use href="#chevron-circle"/></svg></div>
      <div class="row"><span class="row__label">Email</span><span class="row__value">name@sample.io</span><svg width="26" height="26"><use href="#chevron-circle"/></svg></div>
      <div class="row row--links"><span class="row__label">Links</span><span class="row__value">brightpage.net<br>wordtrail.net<br>readnook.net<br><span class="row__add">+ Add link</span></span><span></span></div>
      <div class="row row--bio"><span class="row__label">Bio</span><span class="row__value">A description of this user.</span><svg width="26" height="26"><use href="#chevron-circle"/></svg></div>
    </div>
  </div>
  <nav class="sysnav"><svg width="140" height="12"><use href="#sysnav-icons"/></svg></nav>
</section>

</body>
</html>
```